Fitness website

Website for a fitness brand (see attached specs). Design needs to be modern and vibrant with CTAs on every page. We will provide logos, images, etc but for now user placeholder text and images. For now use the name 'Corvane Athletics' as the name to use on the design. The goal of this site is to either get people to join the gym (5 physical locations across the US); buy an online program; buy merch or supplements or sign up for the newsletter. Pleas use images from this foldeR: https://filebarn.example/share/folders/8QwTz41mKpLrXv93NdYe7HsaBuJ0Cf2_R?usp=sharing

We will be coding this in ReactNative. Lots more work for the winner as well, this is a 1st project for us.

Target Market(s)

fitness enthusiats

Industry/Entity Type

fitness, health, wellness

Number of Pages Required

5+ page

Font styles to use
Other font styles liked:
• Lato

Colors
0054AA
0677BA
7BADD7
CADEEF
E8F1F8
0094D4
00A9DD
6FCCEA
C7EBF8
E9F6FB
00AB8E
00BBA5
67D7C9
C6EFE9
E9F9F6
EE7325
F08F49
F5BC92
FAE3D3
FDF4ED

Requirements
Must have
• must be reactive. most people will view it first on mobile
Nice to have
• video in hero section of top of home page

```html
<!DOCTYPE html>
<html lang="en">
<head>
<meta charset="utf-8">
<title>Corvane Athletics</title>
<link rel="stylesheet" href="https://fonts.googleapis.com/css2?family=Lato:ital,wght@0,300;0,400;0,700;0,900;1,300&display=swap">
<style>
:root{
  --green:#0aa64a;
  --green-text:#17b152;
  --bg:#111111;
  --bg-alt:#161616;
  --card:#1e1e1e;
  --card-media:#333333;
  --line:#2c2c2c;
  --white:#ffffff;
  --muted:#a9a9a9;
  --dim:#8a8a8a;
  --steel:#3d4656;
  --steel-dark:#1a1e25;
  --warm:#5a4436;
}
*{box-sizing:border-box;margin:0;padding:0}
html,body{width:1200px;height:2868px;overflow:hidden}
body{background:var(--bg);color:var(--white);font-family:"Lato",sans-serif;position:relative}
.btn{display:inline-flex;align-items:center;justify-content:center;border-radius:3px;font-weight:700;color:var(--white);text-decoration:none;white-space:nowrap}
.btn-primary{background:var(--green)}
.btn-outline{background:#0d0d0d;border:1px solid #4a4a4a;font-weight:400}
.accent{color:var(--green-text)}

/* hero */
.hero{position:absolute;left:0;top:0;width:1200px;height:638px;overflow:hidden;background:var(--steel-dark)}
.hero-photo{position:absolute;inset:0;
  background:
    radial-gradient(ellipse 260px 300px at 680px 380px,rgba(92,108,132,.75) 0%,rgba(92,108,132,0) 100%),
    radial-gradient(ellipse 230px 300px at 1030px 300px,rgba(110,120,138,.7) 0%,rgba(110,120,138,0) 100%),
    radial-gradient(ellipse 700px 260px at 720px 560px,rgba(70,78,92,.8) 0%,rgba(70,78,92,0) 100%),
    linear-gradient(90deg,#14171c 0%,#222831 35%,#343d4a 70%,#2a313b 100%)}
.nav{position:absolute;left:237px;top:30px;width:726px;height:34px;display:flex;align-items:center}
.logo{font-weight:900;font-size:23px;letter-spacing:-.8px;text-transform:uppercase}
.nav .btn{margin-left:auto;width:106px;height:28px;font-size:12px}
.menu{margin-left:28px;width:20px;height:18px}
.hero-copy{position:absolute;left:237px;top:212px}
.hero-title{font-weight:900;font-size:60px;line-height:61px;text-transform:uppercase;letter-spacing:-1px}
.hero-sub{margin-top:6px;font-size:15.5px;line-height:20px;width:330px}
.hero-ctas{margin-top:30px;display:flex;gap:10px}
.hero-ctas .btn{height:28px;font-size:12px;padding:0 20px}
.hero-ctas .btn-primary{width:130px}

.trust{position:absolute;left:0;top:638px;width:1200px;height:54px;background:#1b1b1b;border-bottom:1px solid var(--line);
  display:flex;align-items:center;justify-content:center;font-size:9px;font-weight:700;letter-spacing:1.6px;color:#b5b5b5}

.section-title{font-weight:900;font-size:38px;text-transform:uppercase;text-align:center;letter-spacing:-.5px}

/* paths */
.paths{position:absolute;left:0;top:692px;width:1200px;height:544px;background:var(--bg)}
.paths .section-title{position:absolute;top:60px;width:100%}
.path-card{position:absolute;top:138px;width:353px;height:345px;background:var(--card);border-radius:4px;overflow:hidden}
.path-card .media{height:198px}
.media-arena{background:
  radial-gradient(ellipse 90px 120px at 185px 100px,rgba(140,120,105,.55) 0%,rgba(140,120,105,0) 100%),
  linear-gradient(180deg,#1c1d22 0%,#2b2d34 55%,#4a4c52 100%)}
.media-coach{background:
  radial-gradient(ellipse 110px 130px at 150px 90px,rgba(120,118,96,.7) 0%,rgba(120,118,96,0) 100%),
  radial-gradient(ellipse 130px 80px at 260px 150px,rgba(160,95,70,.6) 0%,rgba(160,95,70,0) 100%),
  linear-gradient(180deg,#3a3e45 0%,#30333a 100%)}
.path-card h3{margin:24px 20px 0;font-weight:700;font-size:20px;text-transform:uppercase}
.path-card p{margin:10px 20px 0;font-size:10px;line-height:17px;color:var(--muted)}
.path-card .btn{position:absolute;left:20px;right:20px;bottom:20px;height:25px;font-size:10px}

/* featured */
.featured{position:absolute;left:0;top:1236px;width:1200px;height:456px;
  background:
    radial-gradient(ellipse 300px 240px at 960px 300px,rgba(95,70,55,.7) 0%,rgba(95,70,55,0) 100%),
    radial-gradient(ellipse 220px 160px at 700px 90px,rgba(80,62,52,.55) 0%,rgba(80,62,52,0) 100%),
    linear-gradient(90deg,#151515 0%,#1d1c1c 40%,#262321 100%)}
.eyebrow{position:absolute;top:82px;width:100%;text-align:center;font-size:10px;font-weight:700;letter-spacing:1.4px;color:var(--green-text)}
.featured .section-title{position:absolute;top:104px;width:100%;line-height:40px}
.program-box{position:absolute;left:317px;top:196px;width:565px;height:179px;background:rgba(28,28,28,.75);border:1px solid #3a3a3a;border-radius:4px;text-align:center}
.program-box h3{margin-top:30px;font-weight:700;font-size:20px;text-transform:uppercase;color:var(--green-text)}
.program-box p{margin:14px auto 0;width:510px;font-size:11px;line-height:18px;color:#c7c7c7}
.program-box .row{margin-top:18px;display:flex;justify-content:center;gap:6px}
.program-box .btn{height:28px;font-size:9px}
.program-box .btn-primary{width:128px}
.program-box .btn-outline{width:86px}

/* gear */
.gear{position:absolute;left:0;top:1692px;width:1200px;height:512px;background:var(--bg-alt)}
.gear .section-title{position:absolute;top:60px;width:100%}
.gear-card{position:absolute;top:138px;width:228px;height:313px;background:var(--card);border-radius:4px;overflow:hidden}
.gear-card .media{height:228px;background:var(--card-media)}
.gear-card h3{margin:16px 15px 0;font-size:15px;font-weight:700;text-transform:uppercase}
.gear-card .btn{position:absolute;left:15px;right:15px;bottom:14px;height:25px;font-size:10px}

/* testimonial */
.testimonial{position:absolute;left:0;top:2204px;width:1200px;height:290px;
  background:
    radial-gradient(ellipse 500px 90px at 600px 250px,rgba(120,90,95,.55) 0%,rgba(120,90,95,0) 100%),
    radial-gradient(ellipse 200px 140px at 1000px 150px,rgba(120,110,80,.45) 0%,rgba(120,110,80,0) 100%),
    linear-gradient(180deg,#2e3236 0%,#3b3833 55%,#2c2826 100%)}
.testimonial .shade{position:absolute;inset:0;background:rgba(0,0,0,.3)}
.quote{position:absolute;top:70px;width:100%;text-align:center;font-style:italic;font-weight:300;font-size:18px;line-height:23px;color:#e6e6e6}
.cite{position:absolute;top:149px;width:100%;text-align:center;font-size:11px;color:#c9c9c9}
.testimonial .btn{position:absolute;left:548px;top:183px;width:104px;height:24px;font-size:9px}

/* cta */
.cta{position:absolute;left:0;top:2494px;width:1200px;height:265px;background:#1c1c1c;text-align:center}
.cta .section-title{position:absolute;top:55px;width:100%}
.cta h4{position:absolute;top:117px;width:100%;font-size:13px;font-weight:400;letter-spacing:1.4px;color:#cfcfcf}
.cta p{position:absolute;top:146px;width:100%;font-size:10px;color:#b5b5b5}
.signup{position:absolute;left:459px;top:176px;display:flex;gap:11px}
.signup .field{width:174px;height:25px;border:1px solid #3a3a3a;background:#121212;border-radius:2px;font-size:8px;color:#9a9a9a;display:flex;align-items:center;padding-left:8px}
.signup .btn{width:98px;height:25px;font-size:10px}

/* footer */
.footer{position:absolute;left:0;top:2759px;width:1200px;height:109px;background:var(--bg)}
.footer-links,.social{position:absolute;top:33px;display:flex;gap:15px;font-size:9px;color:#a9a9a9}
.footer-links{left:180px}
.social{right:180px;gap:11px;font-size:10px;color:#c9c9c9}
.copyright{position:absolute;top:68px;width:100%;text-align:center;font-size:8px;color:#8a8a8a}
</style>
</head>
<body>

<header class="hero">
  <div class="hero-photo" role="img" aria-label="Athletes lifting a barbell and training on a pull-up rig in a dark gym"></div>
  <nav class="nav">
    <span class="logo">Corvane Athletics</span>
    <a class="btn btn-primary" href="#">Join the Gym</a>
    <svg class="menu" viewBox="0 0 20 18" aria-label="Menu"><g stroke="#fff" stroke-width="2"><line x1="0" y1="2" x2="20" y2="2"/><line x1="0" y1="9" x2="20" y2="9"/><line x1="0" y1="16" x2="20" y2="16"/></g></svg>
  </nav>
  <div class="hero-copy">
    <h1 class="hero-title">Forging<br>Elite<br><span class="accent">Fitness</span></h1>
    <p class="hero-sub">Train where performance is proven. Five U.S. locations or from anywhere in the world.</p>
    <div class="hero-ctas">
      <a class="btn btn-primary" href="#">Browse Programs</a>
      <a class="btn btn-outline" href="#">Shop Gear</a>
    </div>
  </div>
</header>

<div class="trust">TRUSTED BY THE BEST: ELITE ATHLETES · PROFESSIONAL LEAGUES · FITNESS PUBLICATIONS</div>

<section class="paths">
  <h2 class="section-title">Your Path to <span class="accent">Strength</span></h2>
  <article class="path-card" style="left:237px">
    <div class="media media-arena" role="img" aria-label="Athlete skipping rope in a competition arena"></div>
    <h3>Train In Person</h3>
    <p>Experience world-class coaching and community in one of our five state-of-the-art facilities.</p>
    <a class="btn btn-primary" href="#">Find a Location</a>
  </article>
  <article class="path-card" style="left:610px">
    <div class="media media-coach" role="img" aria-label="Coach in a cap guiding athletes through a workout"></div>
    <h3>Train Anywhere</h3>
    <p>Access competitive, functional fitness, specialty, and nutrition programs built by elite coaches.</p>
    <a class="btn btn-primary" href="#">View All Programs</a>
  </article>
</section>

<section class="featured" role="img" aria-label="Athlete mid-workout in a dim gym, background image">
  <div class="eyebrow">FEATURED PROGRAM</div>
  <h2 class="section-title">Elite Performance.<br><span class="accent">Delivered.</span></h2>
  <div class="program-box">
    <h3>The Competitive Track</h3>
    <p>Our flagship program for athletes pushing their limits. Includes daily programming, movement videos, and expert feedback.</p>
    <div class="row">
      <a class="btn btn-primary" href="#">Start Your Program</a>
      <a class="btn btn-outline" href="#">Learn More</a>
    </div>
  </div>
</section>

<section class="gear">
  <h2 class="section-title">Gear <span class="accent">Up</span></h2>
  <article class="gear-card" style="left:237px">
    <div class="media" role="img" aria-label="Apparel product image"></div>
    <h3>Apparel</h3>
    <a class="btn btn-primary" href="#">Shop Apparel</a>
  </article>
  <article class="gear-card" style="left:486px">
    <div class="media" role="img" aria-label="Supplements product image"></div>
    <h3>Supplements</h3>
    <a class="btn btn-primary" href="#">Shop Supplements</a>
  </article>
  <article class="gear-card" style="left:735px">
    <div class="media" role="img" aria-label="Equipment and PDFs product image"></div>
    <h3>Equipment &amp; PDFs</h3>
    <a class="btn btn-primary" href="#">Shop Equipment</a>
  </article>
</section>

<section class="testimonial" role="img" aria-label="Group class stretching together on a gym floor">
  <div class="shade"></div>
  <p class="quote">"Since joining Corvane, I've hit PRs I never thought possible<br>and found a community that pushes me every day."</p>
  <p class="cite">— Maren T.</p>
  <a class="btn btn-outline" href="#">Read Member Stories</a>
</section>

<section class="cta">
  <h2 class="section-title">Ready to <span class="accent">Train?</span></h2>
  <h4>STAY AHEAD OF THE WOD</h4>
  <p>Sign up for our weekly newsletter for exclusive training tips, nutrition guides, and updates.</p>
  <form class="signup">
    <div class="field">Enter Your Email Address</div>
    <a class="btn btn-primary" href="#">Sign Up Now</a>
  </form>
</section>

<footer class="footer">
  <nav class="footer-links"><span>About</span><span>Contact</span><span>Blog</span><span>Locations</span><span>Affiliates</span><span>Privacy Policy</span></nav>
  <nav class="social"><span>Lenswire</span><span>ClipStream</span><span>FriendHub</span><span>Chirp</span></nav>
  <p class="copyright">© 2025 Corvane Athletics. All rights reserved.</p>
</footer>

</body>
</html>
```